VFX Company Business Card Design Project

The Kestrel Works is a decentralized Visual Effects Studio servicing the television and feature film industries.
Project Brief:
Take our logo that was previously designed on Pencil Harbor and make a double sided business card.
Requirements:
- Card MUST be double sided.
- Front of card MUST have the yellow part of our logo against the dark grey background.
- Back of card is completely up to the designer.
- Back of card must include the complete company logo.
Please follow these File Preparation guidelines:
http://printnook.ca/infopage?file=filetype_en&s=PrintNook_new&lang=en
Business

```html
<!DOCTYPE html>
<html lang="en">
<head>
<meta charset="utf-8">
<title>The Kestrel Works – Business Cards</title>
<link rel="stylesheet" href="https://fonts.googleapis.com/css2?family=Jost:wght@400;500;600&display=swap">
<style>
  :root {
    --backdrop: #e8e4de;
    --card: #2b2b2b;
    --yellow: #fcc42a;
    --light: #eef0e8;
    --grey: #6c7276;
    --band: #e8ede4;
    --band-line: #5f6466;
    --ink-dark: #2b2b2b;
  }
  * { box-sizing: border-box; margin: 0; padding: 0; }
  html, body {
    width: 1200px; height: 734px; overflow: hidden;
    background: var(--backdrop);
    font-family: "Jost", "Helvetica Neue", Arial, sans-serif;
  }
  .sheet { position: relative; width: 1200px; height: 734px; }
  .card {
    position: absolute; width: 524px; height: 300px;
    background: var(--card); overflow: hidden;
  }
  .card--front { left: 67px; top: 43px; }
  .card--contact { left: 628px; top: 48px; }
  .card--brand { left: 63px; top: 381px; }
  .card--word { left: 622px; top: 387px; }

  .brand-name { position: absolute; white-space: nowrap; font-weight: 600; letter-spacing: 0.01em; }

  .card--front .brand-name {
    left: 0; right: 0; top: 118px; text-align: center;
    font-size: 46px; color: var(--yellow);
  }

  .card--contact .brand-name {
    left: 48px; top: 118px; font-size: 22px; color: var(--light);
  }
  .divider {
    position: absolute; left: 292px; top: 72px; width: 2px; height: 150px;
    background: linear-gradient(to bottom, transparent, var(--light) 30%, var(--light) 70%, transparent);
  }
  .person { position: absolute; left: 309px; top: 66px; color: var(--light); }
  .person__name { font-size: 20px; font-weight: 500; line-height: 24px; }
  .person__title { font-size: 15px; line-height: 22px; margin-bottom: 9px; }
  .contact-list { list-style: none; font-size: 14px; }
  .contact-list li { display: flex; align-items: center; gap: 5px; height: 20.5px; }
  .contact-list svg { width: 11px; height: 11px; fill: var(--light); flex: none; }
  .address-band {
    position: absolute; left: 0; right: 0; bottom: 0; height: 27px;
    background: var(--band); border-top: 3px solid var(--band-line);
    color: var(--ink-dark); font-size: 14px; text-align: center; line-height: 24px;
  }

  .card--brand .brand-row {
    position: absolute; left: 0; right: 0; top: 122px;
    display: flex; justify-content: center; align-items: center; gap: 16px;
  }
  .card--brand .brand-name { position: static; font-size: 34px; color: var(--light); }
  .mark-dot { width: 34px; height: 34px; border-radius: 50%; background: var(--yellow); }

  .card--word .brand-name {
    left: 0; right: 0; top: 110px; text-align: center;
    font-size: 48px; color: var(--light);
  }
  .web {
    position: absolute; left: 0; right: 0; text-align: center;
    color: var(--light); font-size: 17px; letter-spacing: 0.16em;
  }
  .card--brand .web { top: 255px; }
  .card--word .web { top: 256px; }
</style>
</head>
<body>
<main class="sheet">

  <section class="card card--front" aria-label="Card front">
    <p class="brand-name">The Kestrel Works</p>
  </section>

  <section class="card card--contact" aria-label="Contact card">
    <p class="brand-name">The Kestrel Works</p>
    <div class="divider"></div>
    <div class="person">
      <p class="person__name">Your Name</p>
      <p class="person__title">Title</p>
      <ul class="contact-list">
        <li><svg viewBox="0 0 12 12"><path d="M2.5 1 L4.5 1 L5.2 3.6 L4 4.6 Q5 7 7.4 8 L8.4 6.8 L11 7.5 L11 9.5 Q10.5 11 9 11 Q1 10 1 2.5 Q1 1 2.5 1Z"/></svg>0123 456780</li>
        <li><svg viewBox="0 0 12 12"><path d="M3 1h6a1 1 0 0 1 1 1v8a1 1 0 0 1-1 1H3a1 1 0 0 1-1-1V2a1 1 0 0 1 1-1zm0.5 1.5v6h5v-6z"/></svg>0123 456780</li>
        <li><svg viewBox="0 0 12 12"><path d="M1 3h10v7H1zM1 3l5 4 5-4v1.2L6 8.2 1 4.2z"/></svg>info@kestrelworks.com</li>
        <li><svg viewBox="0 0 12 12"><path d="M6 1a5 5 0 1 0 0 10A5 5 0 0 0 6 1zm0 1.2c.6.7 1 1.8 1.1 3.2H4.9C5 4 5.4 2.9 6 2.2zM2.3 6.6h1.6c.1 1 .4 1.9.8 2.7a3.9 3.9 0 0 1-2.4-2.7zm0-1.2a3.9 3.9 0 0 1 2.4-2.7c-.4.8-.7 1.7-.8 2.7zM6 9.8c-.6-.7-1-1.8-1.1-3.2h2.2C7 8 6.6 9.1 6 9.8zm1.3-.5c.4-.8.7-1.7.8-2.7h1.6a3.9 3.9 0 0 1-2.4 2.7zM8.1 5.4c-.1-1-.4-1.9-.8-2.7a3.9 3.9 0 0 1 2.4 2.7z"/></svg>www.kestrelworks.com</li>
      </ul>
    </div>
    <div class="address-band">00, Complex name, City, State 0042</div>
  </section>

  <section class="card card--brand" aria-label="Card back with name">
    <div class="brand-row">
      <span class="mark-dot"></span>
      <p class="brand-name">The Kestrel Works</p>
    </div>
    <p class="web">www.kestrelworks.com</p>
  </section>

  <section class="card card--word" aria-label="Card back with wordmark">
    <p class="brand-name">The Kestrel Works</p>
    <p class="web">www.kestrelworks.com</p>
  </section>

</main>
</body>
</html>
```